Psychotherapy, Life Coaching, Writer, Motivational Speaker

I am a psychotherapist, life coach, writer and speaker on health and wellness issues. I am a humanist - who believes that we are born to self-actualize - but life - changes that course. That we develop armor and coping mechanisms that divert our growth. I help people examine their road blocks to happiness. My business is unique in that I do concierge therapy. I work intensively - with multi-day sessions, I work internationally through tele-therapy - and traditionally - in an office space. My work is tailored to your needs.

Target Market(s)

Broad

Industry/Entity Type

Health

Contact Information for Business Card

Listen And Grow
Sam Perriton
248 East 39th Street
New York, NY 10027
(305) 555-0173

Requirements
Must have
• Clean lines... not too busy...
• FB page listing: Listen And Grow
• my Web page: www.listenandgrow-example.com
Nice to have
• I would love to be able to list the services: Psychotherapist, Life Coach, Motivational Speaker and Writer - but also don't want a crazy crowded card. Feel free to use the back for description.
Should not have
• Stay away from corny imagery - lotus flowers, zen, lily pond, clouds.

```html
<!DOCTYPE html>
<html lang="en">
<head>
<meta charset="utf-8">
<title>Listen And Grow – Business Card</title>
<link href="https://fonts.googleapis.com/css2?family=Lato:wght@400;700&display=swap" rel="stylesheet">
<style>
  :root {
    --backdrop: #e8e8e8;
    --card: #ffffff;
    --brand-blue: #3f6dab;
    --band-blue: #4a77b2;
    --band-text: #e3ebf6;
    --ink: #1c1c1c;
    --swoosh-dark: #0b0b0f;
  }
  * { margin: 0; padding: 0; box-sizing: border-box; }
  html, body {
    width: 1200px; height: 720px; overflow: hidden;
    background: var(--backdrop);
    font-family: "Lato", Arial, sans-serif;
    color: var(--ink);
  }
  .canvas { position: relative; width: 1200px; height: 720px; }
  .card {
    position: absolute; top: 241px;
    width: 420px; height: 240px;
    background: var(--card);
    border-radius: 14px;
    overflow: hidden;
  }
  .card--front { left: 148px; }
  .card--back { left: 633px; }

  .brand-title {
    position: absolute; left: 15px; top: 16px;
    font-size: 24px; font-weight: 700; color: var(--brand-blue);
    white-space: nowrap;
  }
  .address {
    position: absolute; right: 11px; top: 16px;
    text-align: right; font-size: 12.5px; line-height: 15px;
  }
  .swoosh { position: absolute; left: 0; top: 0; }

  .identity { position: absolute; left: 19px; top: 116px; }
  .identity__name { font-size: 17px; font-weight: 700; color: var(--brand-blue); }
  .identity__creds { font-size: 14px; font-weight: 400; color: var(--ink); }
  .identity__role { font-size: 13px; font-weight: 700; margin-top: 1px; }

  .contact-list {
    position: absolute; left: 20px; top: 162px;
    list-style: none; font-size: 14px; line-height: 16px;
  }
  .contact-list li { display: flex; align-items: center; gap: 4px; }
  .contact-list svg { width: 11px; height: 11px; flex: none; }
  .social-mark { width: 10px; height: 10px; background: var(--brand-blue); border-radius: 1px; flex: none; }

  .back-title {
    position: absolute; left: 0; right: 0; top: 57px;
    text-align: center; font-size: 21px; font-weight: 700; color: var(--brand-blue);
  }
  .appointment {
    position: absolute; left: 0; right: 0; top: 134px;
    text-align: center; font-size: 14px;
  }
  .services-band {
    position: absolute; left: 0; right: 0; bottom: 0; height: 32px;
    background: var(--band-blue); color: var(--band-text);
    font-size: 14px; text-align: center; line-height: 32px;
  }
</style>
</head>
<body>
<main class="canvas">
  <section class="card card--front">
    <svg class="swoosh" width="420" height="240" viewBox="0 0 420 240" aria-hidden="true">
      <defs>
        <linearGradient id="swooshFill" x1="0" y1="0" x2="1" y2="0.4">
          <stop offset="0" stop-color="var(--band-blue)" style="stop-color:#4a77b2"/>
          <stop offset="0.42" stop-color="#3a5f92"/>
          <stop offset="0.7" stop-color="#0b0b0f"/>
          <stop offset="1" stop-color="#2f4f7c"/>
        </linearGradient>
      </defs>
      <path d="M0,57 C130,52 300,92 416,234 C320,150 170,90 0,92 Z" fill="url(#swooshFill)"/>
    </svg>

    <h1 class="brand-title">Listen And Grow</h1>
    <address class="address" style="font-style:normal">248 East 39th Street<br>New York, NY 10027</address>

    <div class="identity">
      <p><span class="identity__name">Sam Perriton,</span> <span class="identity__creds">LMHC, NCC</span></p>
      <p class="identity__role">Psychotherapist.</p>
    </div>

    <ul class="contact-list">
      <li>
        <svg viewBox="0 0 12 12" aria-hidden="true"><path d="M1 4 Q6 0 11 4 L10 5 L8 4 L8 3 Q6 2 4 3 L4 4 L2 5 Z M3 6 H9 L10 11 H2 Z" fill="#3f6dab"/></svg>
        (305) 555-0173
      </li>
      <li>
        <svg viewBox="0 0 12 12" aria-hidden="true"><rect x="0.5" y="2.5" width="11" height="7.5" fill="#3f6dab"/><path d="M0.5 2.5 L6 7 L11.5 2.5" fill="none" stroke="#fff" stroke-width="1"/></svg>
        sperriton.care@example.com
      </li>
      <li>
        <svg viewBox="0 0 12 12" aria-hidden="true"><circle cx="6" cy="6" r="5.2" fill="none" stroke="#3f6dab" stroke-width="1.2"/><ellipse cx="6" cy="6" rx="2.2" ry="5.2" fill="none" stroke="#3f6dab" stroke-width="1"/><path d="M1 6 H11 M2 3.5 H10 M2 8.5 H10" stroke="#3f6dab" stroke-width="0.9"/></svg>
        www.listenandgrow-example.com
      </li>
      <li><span class="social-mark"></span>Listen And Grow</li>
    </ul>
  </section>

  <section class="card card--back">
    <h2 class="back-title">Listen and Grow</h2>
    <p class="appointment">Your Next Appoinment is at...................... at.............. am/pm</p>
    <div class="services-band">Psychotherapy, Coaching, Wellness Media</div>
  </section>
</main>
</body>
</html>
```